New Bicycle shop business card

Hi!
I'm looking for a business card for my new proffesional bike mechanics shop. This shop is only for fixing broken bikes and not selling bikes.
Peferbly a modern and sleek and modern design.
Colors: black, grey, red, white
Information:
Name: Rijwielwerkplaats Vanhoutte
Shop owner: Bart Vanhoutte & Marieke Segers
Website: www.rijwielwerkplaats-vanhoutte.be
Email: info@rijwielwerkplaats-vanhoutte.be
Phone number: +32471902368
Street adres: Kerkweg 46
9940 Bellebeke
Slogan/shop information: Herstellingen van alle merken.
Logo: see files.
Target Market(s)
People who seek a mechanic to fix or upgrade their bikes.
Contact Information for Business Card
Information:
Website: info@rijwielwerkplaats-vanhoutte.be
9940 Bellebeke
Logo: see files.

```html
<!DOCTYPE html>
<html lang="nl">
<head>
<meta charset="utf-8">
<title>Rijwielwerkplaats Vanhoutte – Visitekaartje</title>
<link rel="stylesheet" href="https://fonts.googleapis.com/css2?family=Lato:wght@400;700;900&display=swap">
<style>
  :root {
    --stage: #9a9a9a;
    --paper: #ffffff;
    --ink: #1c1616;
    --red: #e01b3c;
    --night: #221a17;
    --night-pattern: #2b2220;
    --rule: #b9b9b9;
  }
  * { box-sizing: border-box; margin: 0; padding: 0; }
  html, body { width: 1200px; height: 802px; overflow: hidden; }
  body {
    background: var(--stage);
    font-family: "Lato", sans-serif;
    color: var(--ink);
    position: relative;
  }
  .card {
    position: absolute;
    top: 274px;
    width: 442px;
    height: 264px;
    overflow: hidden;
    box-shadow: 2px 3px 6px rgba(0,0,0,0.35);
  }
  .card--front { left: 136px; background: var(--paper); }
  .card--back { left: 624px; background: var(--night); }

  /* front */
  .brand {
    position: absolute;
    left: 8px;
    top: 74px;
    width: 196px;
    text-align: center;
  }
  .brand__dot {
    display: block;
    width: 40px;
    height: 40px;
    margin: 0 auto 14px;
    border-radius: 50%;
    background: var(--red);
  }
  .brand__name {
    font-weight: 900;
    font-size: 16px;
    line-height: 1.2;
    letter-spacing: 0.4px;
    text-transform: uppercase;
    color: var(--ink);
  }
  .divider {
    position: absolute;
    left: 212px;
    top: 72px;
    width: 1px;
    height: 122px;
    background: var(--rule);
  }
  .contact {
    position: absolute;
    left: 222px;
    top: 76px;
    width: 206px;
    font-size: 11.5px;
    line-height: 1.4;
    white-space: nowrap;
  }
  .contact__names {
    color: var(--red);
    font-weight: 700;
    font-size: 10.8px;
    text-transform: uppercase;
  }
  .contact__role { margin-bottom: 6px; }
  .contact__line { display: flex; align-items: center; gap: 5px; }
  .contact__line svg { width: 9px; height: 9px; flex: none; }
  .contact__address { margin-top: 8px; }

  /* back */
  .back__pattern {
    position: absolute;
    inset: 0;
    background: var(--night-pattern);
  }
  .back__content {
    position: absolute;
    inset: 0;
    display: flex;
    flex-direction: column;
    align-items: center;
    justify-content: center;
    text-align: center;
    color: #fff;
  }
  .back__name {
    font-weight: 900;
    font-size: 22px;
    line-height: 1.15;
    letter-spacing: 1px;
    text-transform: uppercase;
  }
  .back__tagline {
    margin-top: 10px;
    font-size: 12.5px;
    text-transform: uppercase;
  }
</style>
</head>
<body>
  <section class="card card--front">
    <div class="brand">
      <span class="brand__dot"></span>
      <div class="brand__name">Rijwielwerkplaats<br>Vanhoutte</div>
    </div>
    <div class="divider"></div>
    <div class="contact">
      <div class="contact__names">Bart Vanhoutte &amp; Marieke Segers</div>
      <div class="contact__role">Owner</div>
      <div class="contact__line">
        <svg viewBox="0 0 10 10"><path fill="var(--red)" d="M1 3c0-1 1-2 4-2s4 1 4 2v1H7V3H3v1H1zM2 5h6l1 4H1z"/></svg>
        +32471902368
      </div>
      <div class="contact__line">
        <svg viewBox="0 0 10 10"><rect x="0.5" y="2" width="9" height="6.5" fill="var(--red)"/><path d="M0.5 2l4.5 3.5L9.5 2" stroke="#fff" stroke-width="0.9" fill="none"/></svg>
        info@rijwielwerkplaats-vanhoutte.be
      </div>
      <div class="contact__line">
        <svg viewBox="0 0 10 10"><circle cx="5" cy="5" r="4.5" fill="var(--red)"/><path d="M3 4.5h4M5 2.5v5" stroke="#fff" stroke-width="0.9"/></svg>
        www.rijwielwerkplaats-vanhoutte.be
      </div>
      <div class="contact__address">Kerkweg 46<br>9940 Bellebeke</div>
    </div>
  </section>

  <section class="card card--back">
    <div class="back__pattern" role="img" aria-label="Repeating pattern of the shop emblem in dark brown"></div>
    <div class="back__content">
      <div class="back__name">Rijwielwerkplaats<br>Vanhoutte</div>
      <div class="back__tagline">Herstellingen van alle merken</div>
    </div>
  </section>
</body>
</html>
```